Business Card for Multi-Brand Sportswear Company

We are looking for a business card which represents our company and the multiple brands within it.

The company: Fen Athletics (LTD)
The brands: Fen, TavaPuni, ElmStretch, Grit and Rain

Employees using these cards would be representing Fen Athletics, rather than any of the individual brands. You will see a current design within the uploaded files, to give some inspiration. The actual text of the brands is not necessary, but the logos should be on there is some format.

Our creative minds on this are stretched, so we are looking for someone to make this their own, and show us what a good business card should look like.

We may like to get these printed with spot gloss, so keep that in mind with your designs.

www.fenathletics.co.uk

Industry/Entity Type

Business

Contact Information for Business Card

Leo Pemberton-Hale
Operations Manager
(+44) 1632 960 418
Leo@fenathletics.co.uk
www.fenathletics.co.uk

Font styles to use
Sans Serif
Other font styles liked:
• Eurostile

Colors
ffffff

Requirements
Nice to have
• Dark (black) background

```html
<!DOCTYPE html>
<html lang="en">
<head>
<meta charset="utf-8">
<title>Fen Athletics – Business Card</title>
<link rel="stylesheet" href="https://fonts.googleapis.com/css2?family=Open+Sans:wght@400;600&display=swap">
<style>
  :root {
    --stage: #454545;
    --paper: #ffffff;
    --brand-red: #ed1c24;
    --ink: #1a1a1a;
    --ink-soft: #5a5a5a;
    --rule: #cfcfcf;
  }
  * { box-sizing: border-box; margin: 0; padding: 0; }
  html, body {
    width: 1105px; height: 1200px; overflow: hidden;
    background: var(--stage);
    font-family: "Open Sans", Arial, sans-serif;
  }
  .card {
    position: absolute;
    left: 196px;
    width: 720px;
    height: 412px;
  }
  .card--front { top: 146px; background: var(--paper); }
  .card--back  { top: 602px; background: var(--brand-red); }

  /* front */
  .front-wordmark {
    position: absolute; left: 57px; top: 190px;
    font-size: 42px; font-weight: 600; color: var(--ink);
    letter-spacing: 0.5px; line-height: 1; white-space: nowrap;
  }
  .front-divider {
    position: absolute; left: 386px; top: 96px;
    width: 1px; height: 214px; background: var(--rule);
  }
  .contact {
    position: absolute; left: 418px; top: 98px;
    color: var(--ink-soft); white-space: nowrap;
  }
  .contact__name {
    font-size: 24px; font-weight: 600; color: var(--brand-red); line-height: 1.2;
  }
  .contact__role {
    font-size: 19px; color: var(--ink); line-height: 1.3; margin-bottom: 12px;
  }
  .contact__address { font-size: 18px; line-height: 1.45; margin-bottom: 6px; }
  .contact__line {
    display: flex; align-items: center; gap: 10px;
    font-size: 18px; line-height: 1.55;
  }
  .contact__icon { width: 16px; height: 16px; flex: none; }

  /* back */
  .back-wordmark {
    position: absolute; left: 0; right: 0; top: 138px;
    text-align: center;
    font-size: 72px; font-weight: 600; color: var(--paper);
    letter-spacing: 1px; line-height: 1; white-space: nowrap;
  }
  .brand-row {
    position: absolute; left: 0; right: 0; top: 322px;
    display: flex; justify-content: center; gap: 30px;
  }
  .brand-row__item {
    display: flex; align-items: center; gap: 8px;
    font-size: 19px; font-weight: 600; color: var(--paper); white-space: nowrap;
  }
  .brand-row__dot {
    width: 14px; height: 14px; border-radius: 50%;
    background: var(--paper); flex: none;
  }
</style>
</head>
<body>

<section class="card card--front">
  <div class="front-wordmark">Fen Athletics</div>
  <div class="front-divider"></div>
  <div class="contact">
    <p class="contact__name">Leo Pemberton-Hale</p>
    <p class="contact__role">Operations Manager</p>
    <p class="contact__address">Ridge Yard, Kelbeck<br>Harlby, ZZ9 4QT</p>
    <p class="contact__line">
      <svg class="contact__icon" viewBox="0 0 16 16" aria-hidden="true">
        <path fill="#ed1c24" d="M3.2 1.2l2.4-.4 1.3 3.2-1.6 1.2c.8 1.8 2.1 3.2 3.9 4l1.3-1.6 3.1 1.4-.4 2.4c-.2.9-1 1.5-1.9 1.4C6 12.4 2.2 8.6 1.8 3.1c-.1-.9.5-1.7 1.4-1.9z"/>
      </svg>
      (+44) 1632 960 418
    </p>
    <p class="contact__line">
      <svg class="contact__icon" viewBox="0 0 16 16" aria-hidden="true">
        <rect x="1" y="3" width="14" height="10" fill="#ed1c24"/>
        <path d="M1.5 3.5L8 9l6.5-5.5" fill="none" stroke="#fff" stroke-width="1.3"/>
      </svg>
      Leo@fenathletics.co.uk
    </p>
    <p class="contact__line">
      <svg class="contact__icon" viewBox="0 0 16 16" aria-hidden="true">
        <circle cx="8" cy="8" r="7" fill="#ed1c24"/>
        <path d="M1 8h14M8 1c-2.5 3-2.5 11 0 14M8 1c2.5 3 2.5 11 0 14" fill="none" stroke="#fff" stroke-width="1"/>
      </svg>
      www.fenathletics.co.uk
    </p>
  </div>
</section>

<section class="card card--back">
  <div class="back-wordmark">Fen Athletics</div>
  <div class="brand-row">
    <span class="brand-row__item"><span class="brand-row__dot"></span>TavaPuni</span>
    <span class="brand-row__item"><span class="brand-row__dot"></span>ElmStretch</span>
    <span class="brand-row__item"><span class="brand-row__dot"></span>Grit and Rain</span>
    <span class="brand-row__item"><span class="brand-row__dot"></span>Fen</span>
  </div>
</section>

</body>
</html>
```